Stationery Design Task - Stationary, memo and report templates for professional services company

Looking for someone to update stationary design but just as importantly come up with a template for reports and memos for use in our consulting firm. Would also like some brand use guidelines to be able to share with our whole team. We have an existing logo that we like. Need to update with a more contemporary look so that our deliverables to clients look good and professional yet stylish. This is for business to business communications. No need for envelope design. Important to have design for multiple pages, i.e. first page of a report and then 2nd page. Need to use in MS word documents so must be easy to use and replicate. Don't want something overly complex. Clean, fresh looking is best.

Industry/Entity Type

Information Technology

Font styles to use
Sans Serif

Colors
33a6d7
0792cd
85cae6
cee9f5
cedeed
85abd2
3377b5
0455a3

Requirements
Must have
• Clean look but with a little style or pop. Something that can easily be used in word documents. Need to have page styles that have a first page of a report (not a cover page) and then secondary page.
Nice to have
• - Although the dark blue is our primary color. Might be willing to look at some accent color as well.
Should not have
• Not just our logo on the page with a color bar.

```html
<!DOCTYPE html>
<html lang="en">
<head>
<meta charset="utf-8">
<title>Crestline Technology – Letterhead</title>
<link href="https://fonts.googleapis.com/css2?family=Open+Sans:wght@400;700&display=swap" rel="stylesheet">
<style>
  :root{
    --bg:#d9d9d9;
    --paper:#ffffff;
    --brand-blue:#0792cd;
    --deep-blue:#0455a3;
    --mid-blue:#3377b5;
    --sky:#85cae6;
    --mist:#dcedf8;
    --grey-line:#b9bcbf;
    --grey-soft:#e6e7e8;
    --text-grey:#6d6e71;
  }
  html,body{margin:0;padding:0;width:1200px;height:784px;overflow:hidden;background:var(--bg);}
  body{font-family:"Open Sans",Arial,sans-serif;}
  .letterhead{
    position:absolute;left:338px;top:22px;width:524px;height:740px;
    background:var(--paper);box-shadow:0 6px 18px rgba(0,0,0,.18);overflow:hidden;
  }
  .letterhead__art{position:absolute;inset:0;}
  .brand{position:absolute;left:36px;top:42px;display:flex;align-items:center;gap:8px;}
  .brand__dot{width:16px;height:16px;border-radius:50%;background:var(--brand-blue);}
  .brand__name{font-weight:700;font-size:17px;line-height:1.05;color:var(--brand-blue);text-transform:uppercase;letter-spacing:.5px;}
  .contact{position:absolute;left:232px;top:44px;font-size:7.6px;line-height:1.55;color:var(--text-grey);}
  .contact__row{display:flex;align-items:center;gap:4px;white-space:nowrap;}
  .contact__row--address{color:var(--brand-blue);font-weight:700;}
  .contact__icon{width:7px;height:7px;flex:none;}
  .ball-placeholder{position:absolute;left:68px;top:362px;width:168px;height:168px;border-radius:50%;
    background:radial-gradient(circle at 55% 45%, #e4e4e4 0%, #ededed 60%, rgba(255,255,255,0) 72%);}
</style>
</head>
<body>
<main class="letterhead">
  <svg class="letterhead__art" viewBox="0 0 524 740" width="524" height="740" aria-hidden="true">
    <!-- edge tabs -->
    <rect x="0" y="10" width="3" height="26" fill="var(--grey-line)"/>
    <rect x="0" y="0" width="3" height="10" fill="var(--brand-blue)"/>
    <rect x="521" y="10" width="3" height="26" fill="var(--grey-line)"/>
    <rect x="521" y="0" width="3" height="10" fill="var(--brand-blue)"/>
    <!-- header divider -->
    <line x1="226" y1="38" x2="214" y2="80" stroke="var(--grey-line)" stroke-width="1"/>
    <!-- light blue wave -->
    <path d="M0 560 C120 610 300 660 524 700 L524 740 L0 740 Z" fill="var(--mist)"/>
    <path d="M0 548 C140 600 320 650 524 690 L524 700 C310 664 130 616 0 566 Z" fill="#ffffff"/>
    <!-- grey swoosh -->
    <path d="M0 470 C40 560 150 610 290 650 C160 624 40 590 0 520 Z" fill="var(--grey-soft)"/>
    <!-- bottom stripes -->
    <g stroke-width="1.6">
      <line x1="0" y1="728" x2="524" y2="728" stroke="var(--deep-blue)"/>
      <line x1="0" y1="724" x2="524" y2="724" stroke="var(--mid-blue)"/>
      <line x1="0" y1="720" x2="524" y2="720" stroke="var(--brand-blue)"/>
      <line x1="0" y1="716" x2="524" y2="716" stroke="#33a6d7"/>
      <line x1="0" y1="712" x2="524" y2="712" stroke="var(--sky)"/>
    </g>
    <rect x="190" y="710" width="150" height="20" fill="#ffffff"/>
    <g stroke-width="1.6">
      <line x1="190" y1="728" x2="340" y2="728" stroke="#8e9194"/>
      <line x1="190" y1="724" x2="340" y2="724" stroke="#a3a6a9"/>
      <line x1="190" y1="720" x2="340" y2="720" stroke="#b6b9bc"/>
      <line x1="190" y1="716" x2="340" y2="716" stroke="#c9cbcd"/>
      <line x1="190" y1="712" x2="340" y2="712" stroke="#dcdddf"/>
    </g>
  </svg>

  <div class="ball-placeholder" role="img" aria-label="Faint decorative brand graphic area"></div>

  <header class="brand">
    <span class="brand__dot"></span>
    <span class="brand__name">Crestline<br>Technology</span>
  </header>

  <address class="contact" style="font-style:normal">
    <div class="contact__row contact__row--address">
      <svg class="contact__icon" viewBox="0 0 10 10"><circle cx="5" cy="5" r="5" fill="var(--brand-blue)"/><circle cx="5" cy="4.3" r="1.6" fill="#fff"/></svg>
      120 Harbor Lane, Brookfield, ST 40210
    </div>
    <div class="contact__row">
      <svg class="contact__icon" viewBox="0 0 10 10"><circle cx="5" cy="5" r="5" fill="var(--brand-blue)"/><rect x="3" y="2.5" width="4" height="5" rx="1" fill="#fff"/></svg>
      (555) 014 2280
      <svg class="contact__icon" viewBox="0 0 10 10"><circle cx="5" cy="5" r="5" fill="var(--brand-blue)"/><rect x="2.5" y="3.2" width="5" height="3.6" fill="#fff"/></svg>
      hello@crestlinetech.com
    </div>
    <div class="contact__row">
      <svg class="contact__icon" viewBox="0 0 10 10"><circle cx="5" cy="5" r="5" fill="var(--sky)"/></svg>
      www.crestlinetech.com
    </div>
  </address>
</main>
</body>
</html>
```